Design the Business card for NetVaultic

Business card required for a professional Cyber Security business.
Company Logo and Icon has already been provided however I would like other options for the logo and icon to compare to. Alternatively, please refine/enhance the image of the logo.icon I have already provided.

If you are going to use the provided logo and icon, I was thinking that the company raised Logo on White background would serve well on the front of the card. See attached. AND, a large company raised stand-alone icon to appear on black background on the back of the card with tagline 'Cyber Risk Management, Governance and Consulting' or 'Cyber Security for your Business' See attached.
Alternatively, provide your own design for the logo and icon.

Target Market(s)

Enterprise, Government, Financial.

Contact Information for Business Card

Tavin Orloweth
Founder and CEO

Email Address
Mobile Number
Website URL
LinkedIn URL

Logo Text

NetVaultic - see attached example of logo

Font styles to use
Other font styles liked:
• Berlin Sans FB

Requirements
Must have
• Clean large and bold icon on the back with tagline.
• Horizontal alignment,
Nice to have
• Round edges.
• Raised Logo/Icon
Should not have
• An unprofessional look and feel.

```html
<!DOCTYPE html>
<html lang="en">
<head>
<meta charset="utf-8">
<title>NetVaultic Business Card</title>
<link rel="stylesheet" href="https://fonts.googleapis.com/css2?family=Cabin:wght@500;700&family=Roboto:wght@400&family=Roboto+Condensed:wght@700&display=swap">
<style>
  :root {
    --page-bg: #e9e6e1;
    --card-white: #f7f7f6;
    --card-black: #1a1b1d;
    --brand-blue: #1a6fc4;
    --tag-blue: #4a6fc9;
    --brand-yellow: #f5b800;
    --text-grey: #555a60;
    --rule-grey: #8f9296;
  }
  * { margin: 0; padding: 0; box-sizing: border-box; }
  html, body { width: 1200px; height: 960px; overflow: hidden; }
  body { background: var(--page-bg); position: relative; font-family: "Roboto", sans-serif; }

  .card {
    position: absolute;
    width: 600px;
    height: 343px;
    box-shadow: 0 3px 8px rgba(0,0,0,0.35);
    overflow: hidden;
  }
  .card-front { left: 314px; top: 113px; background: var(--card-white); }
  .card-back { left: 311px; top: 472px; background: var(--card-black); }

  .wordmark {
    position: absolute;
    display: flex;
    align-items: center;
    gap: 12px;
    font-family: "Cabin", sans-serif;
    font-weight: 700;
    color: var(--brand-blue);
  }
  .card-front .wordmark { right: 40px; top: 48px; font-size: 40px; }
  .wordmark-dot { border-radius: 50%; background: var(--brand-blue); flex: none; }
  .card-front .wordmark-dot { width: 54px; height: 54px; }

  .edge-tab {
    position: absolute;
    left: -14px; top: 171px;
    width: 28px; height: 36px;
    border-radius: 50%;
    background: var(--brand-blue);
  }
  .person { position: absolute; left: 38px; top: 168px; }
  .person-name {
    font-family: "Roboto Condensed", sans-serif;
    font-weight: 700; font-size: 22px;
    color: var(--brand-blue); letter-spacing: 0.2px; line-height: 26px;
  }
  .person-title {
    font-family: "Roboto Condensed", sans-serif;
    font-weight: 700; font-size: 14.5px;
    color: var(--brand-yellow); line-height: 18px;
  }
  .divider {
    position: absolute; left: 40px; top: 218px;
    width: 523px; height: 1.5px; background: var(--rule-grey);
  }
  .contact-list { position: absolute; left: 36px; top: 235px; list-style: none; }
  .contact-list li {
    display: flex; align-items: center; gap: 9px;
    height: 19.3px; font-size: 14px; color: var(--text-grey);
  }
  .contact-list svg { width: 14px; height: 14px; flex: none; }

  .card-back .wordmark {
    left: 0; right: 0; top: 120px;
    justify-content: center; font-size: 44px; gap: 16px;
  }
  .card-back .wordmark-dot { width: 64px; height: 64px; }
  .tagline {
    position: absolute; left: 0; right: 0; top: 276px;
    text-align: center;
    font-family: "Cabin", sans-serif; font-weight: 500; font-size: 18px;
    color: var(--tag-blue);
  }
  .tagline-accent { color: var(--brand-yellow); }
</style>
</head>
<body>
  <section class="card card-front">
    <div class="wordmark"><span class="wordmark-dot"></span>NetVaultic</div>
    <span class="edge-tab"></span>
    <div class="person">
      <div class="person-name">TAVIN ORLOWETH</div>
      <div class="person-title">FOUNDER &amp; CEO</div>
    </div>
    <div class="divider"></div>
    <ul class="contact-list">
      <li>
        <svg viewBox="0 0 14 14"><rect x="3.5" y="0.5" width="7" height="13" rx="1.2" fill="none" stroke="var(--brand-blue)" stroke-width="1.4"/><circle cx="7" cy="11" r="0.9" fill="var(--brand-blue)"/></svg>
        555 014 2738
      </li>
      <li>
        <svg viewBox="0 0 14 14"><rect x="1" y="3" width="12" height="8.5" fill="var(--brand-blue)"/><path d="M1 3 L7 8 L13 3" fill="none" stroke="#fff" stroke-width="1.2"/></svg>
        tavin@netvaultic.com
      </li>
      <li>
        <svg viewBox="0 0 14 14"><circle cx="7" cy="7" r="6" fill="var(--brand-blue)"/><path d="M4 4 Q6 5 5 7 Q7 8 6 11 M9 3 Q10 6 8 7" fill="none" stroke="#fff" stroke-width="1.1"/></svg>
        www.netvaultic.com
      </li>
      <li>
        <svg viewBox="0 0 14 14"><circle cx="7" cy="7" r="6.5" fill="var(--brand-blue)"/><path d="M4.6 6 V10 M7 10 V6" stroke="#fff" stroke-width="1.2"/><circle cx="4.6" cy="4.3" r="0.8" fill="#fff"/></svg>
        netvaultic
      </li>
    </ul>
  </section>

  <section class="card card-back">
    <div class="wordmark"><span class="wordmark-dot"></span>NetVaultic</div>
    <p class="tagline">Cyber Risk Management, <span class="tagline-accent">Governance &amp; Consulting</span></p>
  </section>
</body>
</html>
```